Irrigation Business needs their business cards modernised and revamped

I would like to keep my current logo, colours and revamp the format of the card.

I would like the card to be clean yet important.

Im not sure if you include texture but i would like the named logo to be indented into the card etc.

show me something alive and free something thats clinical to the point yet has a feel of achievement. i would like people to go nice card.

Target Market(s)

high end clients, corporate, sports field manger, the guys that make the decisions

Industry/Entity Type

Business

Contact Information for Business Card

nformation to be included

Dean Harlow (Director)
0487305526
dean@kolvat.biz
www.kestonfieldworks.com

instagram logo
google logo
facebook logo

Colors

Designer to choose colors to be used in the design.

Requirements
Nice to have
• indentations a really nice feel to the card good texture

```html
<!DOCTYPE html>
<html lang="en">
<head>
<meta charset="utf-8">
<title>Keston Fieldworks — Business Card</title>
<link href="https://fonts.googleapis.com/css2?family=Work+Sans:wght@400;500;600&display=swap" rel="stylesheet">
<style>
  :root {
    --backdrop: #1b1c1e;
    --card: #232426;
    --card-edge: #2c2d30;
    --emboss: #55575b;
    --brand-blue: #2f6fbf;
    --sky-blue: #2ea7dc;
    --text-light: #e6e8ec;
    --social-one: #3b5a9a;
    --social-two: #b94c8a;
    --social-three: #d8473a;
  }
  * { margin: 0; padding: 0; box-sizing: border-box; }
  html, body {
    width: 1200px; height: 900px; overflow: hidden;
    background: var(--backdrop);
    font-family: "Work Sans", sans-serif;
  }
  .canvas {
    position: relative; width: 1200px; height: 900px;
    display: flex; flex-direction: column; align-items: center;
    justify-content: center; gap: 40px;
  }
  .card {
    position: relative; width: 700px; height: 400px;
    background: linear-gradient(135deg, var(--card-edge), var(--card) 60%);
    border-radius: 4px;
  }
  /* Front */
  .card-front {
    display: flex; flex-direction: column; align-items: center; justify-content: center; gap: 22px;
  }
  .front-mark {
    width: 96px; height: 96px; border-radius: 50%;
    background: var(--emboss);
  }
  .front-name {
    font-weight: 600; font-size: 34px; letter-spacing: 2px;
    text-transform: uppercase; color: var(--emboss);
  }
  /* Back */
  .card-back {
    display: flex; align-items: center; padding: 0 0 0 120px;
  }
  .brand-block {
    display: flex; flex-direction: column; align-items: center; gap: 12px; width: 170px;
  }
  .brand-mark {
    width: 150px; height: 150px; border-radius: 50%;
    background: var(--sky-blue);
  }
  .brand-name {
    font-size: 13px; font-weight: 500; letter-spacing: 1.5px;
    text-transform: uppercase; color: var(--sky-blue);
  }
  .divider {
    width: 2px; height: 130px; background: var(--sky-blue); margin: 0 30px 0 30px;
  }
  .contact-person { color: var(--text-light); }
  .person-name {
    font-size: 26px; font-weight: 500; color: var(--brand-blue);
    text-transform: uppercase; letter-spacing: 0.5px;
  }
  .person-role { font-size: 19px; margin-bottom: 18px; }
  .contact-list { list-style: none; display: flex; flex-direction: column; gap: 6px; }
  .contact-item {
    display: flex; align-items: center; gap: 14px;
    font-size: 18px; font-weight: 400; letter-spacing: 0.6px;
  }
  .contact-icon { width: 18px; height: 18px; flex: none; }
  .social-row {
    position: absolute; left: 50%; bottom: 42px; transform: translateX(-50%);
    display: flex; gap: 10px;
  }
  .social-dot { width: 24px; height: 24px; border-radius: 50%; }
  .social-dot.one { background: var(--social-one); border-radius: 4px; }
  .social-dot.two { background: var(--social-two); border-radius: 6px; }
  .social-dot.three { background: var(--social-three); }
</style>
</head>
<body>
<main class="canvas">
  <section class="card card-front">
    <div class="front-mark"></div>
    <div class="front-name">Keston Fieldworks</div>
  </section>

  <section class="card card-back">
    <div class="brand-block">
      <div class="brand-mark"></div>
      <div class="brand-name">Keston Fieldworks</div>
    </div>
    <div class="divider"></div>
    <div class="contact-person">
      <div class="person-name">Dean Harlow</div>
      <div class="person-role">Director</div>
      <ul class="contact-list">
        <li class="contact-item">
          <svg class="contact-icon" viewBox="0 0 24 24"><path fill="#2ea7dc" d="M6.6 10.8a15 15 0 0 0 6.6 6.6l2.2-2.2a1 1 0 0 1 1-.25 11.4 11.4 0 0 0 3.6.57 1 1 0 0 1 1 1V20a1 1 0 0 1-1 1A17 17 0 0 1 3 4a1 1 0 0 1 1-1h3.5a1 1 0 0 1 1 1c0 1.25.2 2.45.57 3.6a1 1 0 0 1-.25 1z"/></svg>
          <span>0487305526</span>
        </li>
        <li class="contact-item">
          <svg class="contact-icon" viewBox="0 0 24 24"><rect x="2" y="5" width="20" height="14" rx="1" fill="#2ea7dc"/><path d="M2 6l10 7 10-7" fill="none" stroke="#232426" stroke-width="1.8"/></svg>
          <span>dean@kolvat.biz</span>
        </li>
        <li class="contact-item">
          <svg class="contact-icon" viewBox="0 0 24 24" fill="none" stroke="#2ea7dc" stroke-width="1.6"><circle cx="12" cy="12" r="9"/><ellipse cx="12" cy="12" rx="4" ry="9"/><path d="M3 12h18M5 7h14M5 17h14"/></svg>
          <span>www.kestonfieldworks.com</span>
        </li>
      </ul>
    </div>
    <div class="social-row">
      <span class="social-dot one"></span>
      <span class="social-dot two"></span>
      <span class="social-dot three"></span>
    </div>
  </section>
</main>
</body>
</html>
```